Fizz's Shed & Grill Burger Restaurant Website - HomePage Only PSD

I need a website design for a restaurant called "Fizz's Shed and Grill" featuring burgers, wings, beer, live music, trivia, and more. I have several images of the restaurant and they already have their logo files created (see attached). I want some type of wood background and integrate the silver tin. This needs to be a modern, hip and fun type design. Design must incorporate these attached graphics.

UPDATE - just added a few more images of things I really like to be incorporated into my designs.
Updates

Industry/Entity Type

Burger Restaurant

Number of Pages Required

1 page

Font styles to use
Sans Serif

Requirements
Must have
• Restaurant/Bar theme with integration of existing logo and the red wood look.
Nice to have
• - Modern Fun appearance
• - Use Pelko Fonts

```html
<!DOCTYPE html>
<html lang="en">
<head>
<meta charset="utf-8">
<title>Fizz's Shed and Grill</title>
<link href="https://fonts.googleapis.com/css2?family=Tinos:wght@400;700&family=Open+Sans:ital,wght@0,400;0,600;1,400&display=swap" rel="stylesheet">
<style>
:root{
  --wood-dark:#130b06;
  --wood-mid:#24160c;
  --wood-foot:#3a2414;
  --orange:#e9a21c;
  --white:#ffffff;
  --text:#e6e0d8;
  --red:#c8201f;
  --silver:#b9b9b9;
  --silver-dark:#7d7d7d;
  --bar:#1a0f08;
}
*{box-sizing:border-box;margin:0;padding:0}
html,body{width:1200px;height:2332px;overflow:hidden}
body{
  position:relative;
  font-family:"Open Sans",Arial,sans-serif;
  color:var(--text);
  background:
    repeating-linear-gradient(180deg,transparent 0 120px,rgba(0,0,0,.55) 120px 123px),
    radial-gradient(ellipse at 50% 40%,#3b2614 0%,var(--wood-mid) 45%,var(--wood-dark) 100%);
}
.abs{position:absolute}
.serif{font-family:"Tinos","Times New Roman",serif}

/* header */
.brand{left:531px;top:34px;width:138px;height:138px;border:3px solid #ddd;border-radius:50%;
  display:flex;align-items:center;justify-content:center;text-align:center;
  font-family:"Tinos",serif;font-weight:700;font-size:20px;line-height:1.15;color:#e8e8e8}
.nav{top:228px;left:0;width:1200px;height:30px}
.nav a{position:absolute;font-family:"Tinos",serif;font-size:19px;color:var(--white);text-decoration:none;letter-spacing:.3px}
.nav a.active{color:var(--orange)}

/* slider */
.frame-back{background:linear-gradient(135deg,#d8d8d8,#8d8d8d);box-shadow:0 6px 14px rgba(0,0,0,.6)}
.slide{left:101px;top:305px;width:995px;height:458px;background:linear-gradient(135deg,#e2e2e2,#9a9a9a);padding:8px;box-shadow:0 8px 18px rgba(0,0,0,.7)}
.slide-photo{width:100%;height:100%;background:radial-gradient(ellipse at 55% 45%,#c79a5c 0%,#8a5a2e 40%,#3a2313 100%);position:relative}
.slide-title{left:30px;top:328px;font-family:"Tinos",serif;font-size:45px;color:var(--orange)}
.slide-sub{left:30px;top:385px;font-family:"Tinos",serif;font-size:27px;color:var(--white)}
.dots{right:18px;bottom:22px;display:flex;gap:6px}
.dots span{width:8px;height:8px;border-radius:50%;background:rgba(255,255,255,.35)}
.dots span:first-child{background:var(--orange)}

/* welcome */
.welcome{top:800px;left:0;width:1200px;text-align:center}
.welcome h1{font-family:"Tinos",serif;font-weight:700;font-size:35px;color:var(--white);line-height:42px}
.welcome h2{font-family:"Tinos",serif;font-weight:700;font-size:41px;color:var(--orange);line-height:46px}
.welcome p{width:830px;margin:18px auto 0;font-size:12.5px;line-height:25px;color:var(--text)}

/* specials */
.special{top:1041px;width:322px;height:292px;background:linear-gradient(135deg,#d0d0d0,#808080);padding:9px;box-shadow:0 6px 14px rgba(0,0,0,.6)}
.special-photo{height:198px}
.special-band{height:76px;background:var(--red);text-align:center;padding-top:16px}
.special-band h3{font-family:"Tinos",serif;font-weight:400;font-size:19px;color:var(--white)}
.special-band span{display:block;font-family:"Tinos",serif;font-size:10px;color:#f5dada;margin-top:4px}
.badge{top:-17px;right:-7px;width:106px;height:106px;border-radius:50%;background:var(--orange);
  display:flex;align-items:center;justify-content:center;text-align:center;font-family:"Tinos",serif;font-size:18px;line-height:23px;color:var(--white);
  box-shadow:0 0 0 4px rgba(233,162,28,.5)}

/* about */
.about-photo{left:93px;top:1409px;width:322px;height:258px;background:linear-gradient(135deg,#d0d0d0,#808080);padding:8px;box-shadow:0 6px 14px rgba(0,0,0,.6)}
.about-title{left:458px;top:1413px;font-family:"Tinos",serif;font-weight:700;font-size:26px;color:var(--orange)}
.about-text{left:462px;top:1462px;width:640px;font-size:12.5px;line-height:24.5px;color:var(--text)}
.btn{left:460px;top:1604px;width:163px;height:46px;background:linear-gradient(#e4e4e4,#9d9d9d);border:1px solid #666;
  font-family:"Tinos",serif;font-size:14px;color:#333;display:flex;align-items:center;justify-content:center}

/* testimonials */
.happy{top:1718px;left:0;width:1200px;text-align:center;font-family:"Tinos",serif;font-weight:700;font-size:28px;color:var(--orange)}
.avatar{width:164px;height:164px;border-radius:50%;background:linear-gradient(135deg,#e0e0e0,#8a8a8a);padding:8px}
.avatar div{width:100%;height:100%;border-radius:50%}
.client-name{font-family:"Tinos",serif;font-weight:700;font-size:17px;color:var(--orange)}
.client-role{font-size:12.5px;color:var(--orange);margin-top:4px}
.client-quote{font-style:italic;font-size:11.5px;line-height:22.5px;color:var(--text);margin-top:12px;width:300px}
.arrow{font-size:22px;color:#555}

/* footer */
.footer{top:2028px;left:0;width:1200px;height:249px;
  background:repeating-linear-gradient(90deg,var(--wood-foot) 0 74px,#2a1a0e 74px 77px),var(--wood-foot)}
.fcol{top:2072px}
.fcol h4{font-family:"Tinos",serif;font-weight:700;font-size:16px;color:var(--orange);margin-bottom:9px}
.fcol li{list-style:none;font-size:11.5px;line-height:25.6px;color:var(--white)}
.fcol .name{color:var(--orange);font-weight:600}
.fcol .icon{display:inline-block;width:14px;margin-right:8px;vertical-align:middle}
.email{left:786px;top:2135px;width:308px;height:34px;background:#d9d9d9;border:1px solid #aaa;font-size:11px;color:#888;padding:9px 12px}
.subscribe{left:786px;top:2183px;width:128px;height:36px;background:linear-gradient(#e4e4e4,#9d9d9d);border:1px solid #666;
  font-family:"Tinos",serif;font-size:13px;color:#333;display:flex;align-items:center;justify-content:center}
.bottom{top:2277px;left:0;width:1200px;height:55px;background:var(--bar);text-align:center;font-size:11.5px;line-height:55px;color:var(--white)}
</style>
</head>
<body>

<header>
  <div class="abs brand">Fizz's<br>Shed &amp;<br>Grill</div>
  <nav class="abs nav">
    <a class="active" style="left:137px">HOME</a>
    <a style="left:272px">ABOUT US</a>
    <a style="left:445px">SERVICES</a>
    <a style="left:613px">MENUS</a>
    <a style="left:744px">TESTIMONIALS</a>
    <a style="left:945px">CONTACT US</a>
  </nav>
</header>

<section class="hero">
  <div class="abs frame-back" style="left:118px;top:290px;width:975px;height:470px;transform:rotate(-1.2deg)"></div>
  <div class="abs frame-back" style="left:95px;top:300px;width:1005px;height:470px;transform:rotate(.8deg)"></div>
  <div class="abs slide">
    <div class="slide-photo" role="img" aria-label="Close-up of cheeseburger sliders with red onion">
      <div class="abs slide-title">Fizz's Shed and Grill</div>
      <div class="abs slide-sub">Our restaurant is about burgers, wings, beer, live music, trivia, etc.</div>
      <div class="abs dots"><span></span><span></span><span></span></div>
    </div>
  </div>
</section>

<section class="abs welcome">
  <h1>WELCOME TO</h1>
  <h2>FIZZ'S SHED AND GRILL</h2>
  <p>Lorem Ipsum is simply dummy text of the printing and typesetting industry. Lorem Ipsum has been the industry's standard dummy text ever since the 1500s, when an unknown printer took a galley of type and scrambled it to make a type specimen book. It has survived not only five centuries, but also the leap into electronic typesetting...</p>
</section>

<section class="specials">
  <div class="abs special" style="left:93px">
    <div class="special-photo" role="img" aria-label="Loaded burger with lettuce and tomato" style="background:radial-gradient(ellipse at 45% 55%,#c2833a,#7a3c1a 60%,#3a1a0c)"></div>
    <div class="special-band"><h3>MEAT BURGERS</h3><span>— CLICK HERE FOR VIEW DETAILS —</span></div>
    <div class="abs badge">OUR<br>SPECIAL</div>
  </div>
  <div class="abs special" style="left:437px">
    <div class="special-photo" role="img" aria-label="Glazed chicken wings on lettuce" style="background:radial-gradient(ellipse at 50% 50%,#a8451c,#6b2410 60%,#3a2a14)"></div>
    <div class="special-band"><h3>WINGS</h3><span>— CLICK HERE FOR VIEW DETAILS —</span></div>
    <div class="abs badge">OUR<br>SPECIAL</div>
  </div>
  <div class="abs special" style="left:779px">
    <div class="special-photo" role="img" aria-label="Mugs of dark and golden beer" style="background:radial-gradient(ellipse at 55% 55%,#e0a030,#8a4a12 55%,#2a140a)"></div>
    <div class="special-band"><h3>BEER</h3><span>— CLICK HERE FOR VIEW DETAILS —</span></div>
    <div class="abs badge">OUR<br>SPECIAL</div>
  </div>
</section>

<section class="about">
  <div class="abs about-photo"><div role="img" aria-label="Restaurant front with red roof and cow statue" style="width:100%;height:100%;background:linear-gradient(180deg,#b85a4a 0%,#9c8a78 35%,#6e6a5a 70%,#5c6a40 100%)"></div></div>
  <h2 class="abs about-title">ABOUT FIZZ'S SHED AND GRILL</h2>
  <p class="abs about-text">Lorem Ipsum is simply dummy text of the printing and typesetting industry. Lorem Ipsum has been the industry's standard dummy text ever since the 1500s, when an unknown printer took a galley of type and scrambled it to make a type specimen book. It has survived not only five centuries, but also the leap into electronic typesetting, remaining essentially unchanged. It was popularised in the 1960s with the release of Letraset sheets containing Lorem Ipsum passages, and more recently with desktop publishing software like Aldus PageMaker including versions of Lorem Ipsum.</p>
  <div class="abs btn">READ MORE INFO</div>
</section>

<section class="testimonials">
  <h2 class="abs happy">HAPPY CLIENT'S</h2>
  <div class="abs arrow" style="left:66px;top:1860px">‹</div>
  <div class="abs arrow" style="left:1126px;top:1860px">›</div>

  <div class="abs avatar" style="left:100px;top:1791px"><div role="img" aria-label="Portrait of a smiling male client" style="background:linear-gradient(135deg,#7a5a44,#3c2c22)"></div></div>
  <div class="abs" style="left:295px;top:1810px">
    <div class="client-name">MARLON REYES</div>
    <div class="client-role">Business man</div>
    <p class="client-quote">Lorem Ipsum is simply dummy text of the printing and typesetting industry. Lorem Ipsum has been the industry's standard dummy text ever since the 1500s, when an unknown printer took a galley...</p>
  </div>

  <div class="abs avatar" style="left:622px;top:1791px"><div role="img" aria-label="Portrait of a smiling female client" style="background:linear-gradient(135deg,#a07058,#5a3a2a)"></div></div>
  <div class="abs" style="left:817px;top:1810px">
    <div class="client-name">MARLON REYES</div>
    <div class="client-role">Business man</div>
    <p class="client-quote">Lorem Ipsum is simply dummy text of the printing and typesetting industry. Lorem Ipsum has been the industry's standard dummy text ever since the 1500s, when an unknown printer took a galley...</p>
  </div>
</section>

<footer>
  <div class="abs footer"></div>
  <div class="abs fcol" style="left:101px">
    <h4>WELCOME</h4>
    <ul><li>Home</li><li>About Us</li><li>Services</li><li>Menus</li><li>Testimonials</li><li>Contact Us</li></ul>
  </div>
  <div class="abs fcol" style="left:297px">
    <h4>CONTACT INFO</h4>
    <ul>
      <li class="name">Fizz's Shed and Grill</li>
      <li style="line-height:21px">48 Plank Road, Oakvale,<br>Country : 5550214</li>
      <li><svg class="icon" viewBox="0 0 16 16" width="14" height="14"><path fill="#e9a21c" d="M3 1l3 0 1 4-2 1.5c1 2 2.5 3.5 4.5 4.5L11 9l4 1v3c0 1-1 2-2 2C7 15 1 9 1 3c0-1 1-2 2-2z"/></svg>( 5550 ) 214 870</li>
      <li><svg class="icon" viewBox="0 0 16 16" width="14" height="14"><rect x="1" y="3" width="14" height="10" fill="#e9a21c"/><path d="M1 3l7 5 7-5" stroke="#3a2414" stroke-width="1.4" fill="none"/></svg>info@fizzsshedgrill.com</li>
    </ul>
  </div>
  <div class="abs fcol" style="left:555px">
    <h4>INFORMATION</h4>
    <ul><li>Terms &amp; Conditions</li><li>Privacy Policy</li><li>Disclaimer</li><li>Sitemap</li></ul>
  </div>
  <div class="abs fcol" style="left:786px">
    <h4>NEWSLETTER SIGNUP</h4>
    <ul><li>Get our recent updates through your email id</li></ul>
  </div>
  <div class="abs email">Enter your email id</div>
  <div class="abs subscribe">SUBSCRIBE</div>
  <div class="abs bottom">© 2016. Fizz's Shed and Grill. All Rights Reserved.</div>
</footer>

</body>
</html>
```